THE PAPER HERONS - CREATIVE MINDS WHO LIFT DESIGN TO A FINE ART.

Coffee-table book format.Will feature 20 'design' companies, one from each of 20 categories:3D Design . Branding Design . Broadcast Design . Communication . Digital Design Fashion . Exhibition Design . Furniture Design . Graphic Design . Industrial Design Interior Design . Jewelry . Lighting Design . Package Design . Retail Design . Sustainable Design . Urban Design . Web Design . Yacht DesignWant an eye-catching photo(s), design, etc. This will involve some creative effort.
Updates

After some thought, decided something that is a common thread through all design industries. A nice desk, upon which is a blank sketch pad, a pencil, and beside them a computer. A designer has a new idea, uses the sketch pad, then moves on to the computer to develop his/her idea. Cheers, Gordon

Target Market(s)

US professionals who own companies involved in the world of design.

Requirements
Must have
• Format is 11 in wide and 10 inches high cover.
• Photograph(s) or artwork that will catch the eye of the
• readers browsing the book sections.

```html
<!DOCTYPE html>
<html lang="en">
<head>
<meta charset="utf-8">
<title>The Paper Herons — Book Cover</title>
<link rel="stylesheet" href="https://fonts.googleapis.com/css2?family=Montserrat:wght@300;400&display=swap">
<style>
  :root {
    --page-bg: #ffffff;
    --cover-bg: #eef4f4;
    --author-green: #1f7a4c;
    --ink: #141414;
    --tool-wood: #b9824f;
    --tool-dark: #3b2a22;
    --tool-yellow: #e4c44a;
    --tool-violet: #5a3b5e;
    --tool-teal: #7fb9c4;
  }
  html, body {
    margin: 0;
    padding: 0;
    width: 1200px;
    height: 947px;
    overflow: hidden;
    background: var(--page-bg);
  }
  .canvas {
    position: relative;
    width: 1200px;
    height: 947px;
  }
  .cover {
    position: absolute;
    left: 160px;
    top: 73px;
    width: 880px;
    height: 800px;
    background: var(--cover-bg);
    overflow: hidden;
    font-family: "Montserrat", Arial, sans-serif;
    text-align: center;
  }
  .cover__author {
    position: absolute;
    top: 42px;
    left: 0;
    right: 0;
    margin: 0;
    font-size: 34px;
    line-height: 40px;
    font-weight: 400;
    letter-spacing: 2px;
    color: var(--author-green);
  }
  .cover__title {
    position: absolute;
    top: 142px;
    left: 0;
    right: 0;
    margin: 0;
    font-size: 66px;
    line-height: 66px;
    font-weight: 300;
    letter-spacing: 3px;
    color: var(--ink);
  }
  .cover__subtitle {
    position: absolute;
    top: 306px;
    left: 0;
    right: 0;
    margin: 0;
    font-size: 24px;
    line-height: 34px;
    font-weight: 300;
    letter-spacing: 1px;
    color: var(--ink);
  }
  .cover__photo {
    position: absolute;
    left: 300px;
    top: 420px;
    width: 580px;
    height: 380px;
  }
</style>
</head>
<body>
  <main class="canvas">
    <section class="cover">
      <p class="cover__author">GORDON ASHWORTH</p>
      <h1 class="cover__title">THE PAPER<br>HERONS</h1>
      <p class="cover__subtitle">CREATIVE MINDS WHO<br>LIFT DESIGN TO A FINE ART</p>
      <svg class="cover__photo" role="img" aria-label="Photograph of a pot of artist tools: a fountain pen, a wide paintbrush, pencils, pastels and markers" viewBox="0 0 580 380" preserveAspectRatio="none">
        <defs>
          <linearGradient id="toolTones" x1="0" y1="0" x2="1" y2="0">
            <stop offset="0" stop-color="var(--tool-yellow)"/>
            <stop offset="0.25" stop-color="var(--tool-dark)"/>
            <stop offset="0.45" stop-color="var(--tool-wood)"/>
            <stop offset="0.6" stop-color="var(--tool-violet)"/>
            <stop offset="0.75" stop-color="var(--tool-wood)"/>
            <stop offset="0.9" stop-color="var(--tool-teal)"/>
            <stop offset="1" stop-color="var(--tool-dark)"/>
          </linearGradient>
          <linearGradient id="topFade" x1="0" y1="0" x2="0" y2="1">
            <stop offset="0" stop-color="#fff" stop-opacity="0"/>
            <stop offset="0.3" stop-color="#fff" stop-opacity="0.85"/>
            <stop offset="1" stop-color="#fff" stop-opacity="1"/>
          </linearGradient>
          <mask id="photoFade">
            <rect width="580" height="380" fill="url(#topFade)"/>
          </mask>
        </defs>
        <rect width="580" height="380" fill="url(#toolTones)" mask="url(#photoFade)"/>
      </svg>
    </section>
  </main>
</body>
</html>
```